New Business Card Design Project

I need a design for business cards, i am an electrical business called "Corvane Electrical and Communications" i need the cards to be double sided with the company logo on the back (attached) the front needs to say my company name, web site, email address, telephone number, and ABN number and electrical license number. I am open to different arrangements of the information but would like the background to be incorporating something electrical or something that looks smart. open to all additional ideas also.

The company colours are orange and grey see logo attached.

Business Name: Corvane Electrical and Communications
Website: corvaneelectricalandcomms.example.com.au
Email: brent@corvaneelectricalandcomms.example.com.au
Telephone(mobile): 0481209736
ABN: 71208349162
Lic No: 418273D

Target Market(s)

Business entities, Project Managers, Accounts, Clients

Industry/Entity Type

Electrician

Contact Information for Business Card

I need a design for business cards, i am an electrical business called "Corvane Electrical and Communications" i need the cards to be double sided with the company logo on the back (attached) the front needs to say my company name

Font styles to use
Serif
Sans Serif

Colors
f37122
5c5c5c

Requirements
Must have
• Must have the Logo on the back open to different ways of it being on the back but had in mind to keep it central but again open to other options
Nice to have
• A real modern cool background that is eye catching yet contemporary
Should not have
• No backgrounds of a light bulb or plug or anything like that

```html
<!DOCTYPE html>
<html lang="en">
<head>
<meta charset="utf-8">
<title>Corvane Electrical and Communications – Business Cards</title>
<link rel="stylesheet" href="https://fonts.googleapis.com/css2?family=Questrial&display=swap">
<style>
  :root {
    --backdrop: #2b2b2b;
    --card: #050505;
    --orange: #f5a623;
    --white: #ffffff;
    --grey: #5c5c5c;
  }
  * { box-sizing: border-box; margin: 0; padding: 0; }
  html, body {
    width: 1200px; height: 900px; overflow: hidden;
    background: var(--backdrop);
    font-family: "Questrial", sans-serif;
  }
  .canvas {
    width: 1200px; height: 900px;
    display: flex; flex-direction: column; align-items: center; justify-content: center;
    gap: 40px;
  }
  .card {
    position: relative;
    width: 700px; height: 400px;
    background: var(--card);
    overflow: hidden;
    box-shadow: 0 10px 30px rgba(0,0,0,.5);
  }

  /* Logo side */
  .brand-name {
    position: absolute; left: 0; right: 0; top: 118px;
    display: flex; align-items: center; justify-content: center; gap: 16px;
  }
  .brand-dot { width: 22px; height: 22px; border-radius: 50%; background: var(--orange); flex: none; }
  .brand-text {
    color: var(--white); font-size: 40px; letter-spacing: 1px; line-height: 1.15;
    text-transform: uppercase; text-align: left; white-space: nowrap;
  }
  .web-band {
    position: absolute; left: 0; right: 0; bottom: 0; height: 52px;
    display: grid; grid-template-columns: 14% 64% 22%;
  }
  .web-band .band-white { background: var(--white); }
  .web-band .band-orange {
    background: var(--orange); color: var(--white);
    display: flex; align-items: center; justify-content: center;
    font-size: 16px; letter-spacing: .3px;
  }

  /* Contact side */
  .front .brand-name {
    top: 70px; left: 48px; right: auto; justify-content: flex-start; gap: 10px;
  }
  .front .brand-dot { width: 14px; height: 14px; }
  .front .brand-text { font-size: 20px; letter-spacing: .5px; }
  .licence {
    position: absolute; left: 48px; top: 134px;
    font-size: 18px; color: var(--white);
  }
  .licence .label, .contact .label { color: var(--orange); }
  .accent-lines { position: absolute; inset: 0; }
  .person {
    position: absolute; right: 148px; top: 92px; text-align: right;
  }
  .person-name { color: var(--orange); font-size: 24px; letter-spacing: .5px; white-space: nowrap; }
  .person-role {
    position: absolute; right: 120px; top: 133px;
    color: var(--white); font-size: 11px; letter-spacing: 1px;
  }
  .contact {
    position: absolute; left: 48px; bottom: 36px;
    list-style: none; color: var(--white); font-size: 15px; line-height: 1.6;
  }
  .contact li { display: flex; align-items: center; gap: 10px; }
  .contact svg { width: 12px; height: 12px; fill: var(--orange); flex: none; }
</style>
</head>
<body>
<main class="canvas">

  <section class="card back" aria-label="Card back">
    <div class="brand-name">
      <span class="brand-dot"></span>
      <span class="brand-text">Corvane Electrical<br>and Communications</span>
    </div>
    <div class="web-band">
      <span class="band-white"></span>
      <span class="band-orange">www.corvaneelectricalandcomms.example.com.au</span>
      <span class="band-white"></span>
    </div>
  </section>

  <section class="card front" aria-label="Card front">
    <div class="brand-name">
      <span class="brand-dot"></span>
      <span class="brand-text">Corvane Electrical<br>and Communications</span>
    </div>
    <p class="licence"><span class="label">Lic No:</span> 418273D</p>

    <svg class="accent-lines" viewBox="0 0 700 400" aria-hidden="true">
      <polyline points="0,250 580,128 700,128" fill="none" stroke="var(--orange)" stroke-width="1.5"/>
    </svg>

    <div class="person">
      <p class="person-name">MARLO FENWICK</p>
    </div>
    <p class="person-role">DIRECTOR</p>

    <ul class="contact">
      <li><span class="label">ABN:</span> 71208349162</li>
      <li>
        <svg viewBox="0 0 24 24"><path d="M6.6 10.8a15.1 15.1 0 0 0 6.6 6.6l2.2-2.2a1 1 0 0 1 1-.25 11.4 11.4 0 0 0 3.6.57 1 1 0 0 1 1 1V20a1 1 0 0 1-1 1A17 17 0 0 1 3 4a1 1 0 0 1 1-1h3.5a1 1 0 0 1 1 1c0 1.25.2 2.45.57 3.6a1 1 0 0 1-.25 1z"/></svg>
        0481 209 736
      </li>
      <li>
        <svg viewBox="0 0 24 24"><path d="M2 5h20v14H2z M3.5 6.5 12 13l8.5-6.5" stroke="#050505" stroke-width="1.5"/></svg>
        brent@corvaneelectricalandcomms.example.com.au
      </li>
      <li>
        <svg viewBox="0 0 24 24"><circle cx="12" cy="12" r="10"/><path d="M2 12h20M12 2c3 3 3 17 0 20M12 2c-3 3-3 17 0 20" fill="none" stroke="#050505" stroke-width="1.4"/></svg>
        www.corvaneelectricalandcomms.example.com.au
      </li>
    </ul>
  </section>

</main>
</body>
</html>
```